Professional & attention grabbing.

A business card design, front and back. I already have a logo I will attach, but I am open to something new as well.
Things to include:
Name:
Title:
Phone:
Email:
Wanting something that is professional but attention grabbing.
Also we do a lot of work using drones on natural gas pipelines (leading the future)if you want to include any of that. I'm open to ideas.
Target Market(s)
Natural gas transmission industry / greenhouse gas mitigation industry
Industry/Entity Type
Business
Colors
Designer to choose colors to be used in the design.
Look and feel
Each slider illustrates characteristics of the customer's brand and the style your logo design should communicate.

```html
<!DOCTYPE html>
<html lang="en">
<head>
<meta charset="utf-8">
<title>Kestrany Inspections — Business Card</title>
<link rel="stylesheet" href="https://fonts.googleapis.com/css2?family=Source+Sans+3:ital,wght@0,400;0,600;1,400&display=swap">
<style>
  :root {
    --backdrop: #e6e6e6;
    --paper: #ffffff;
    --charcoal: #39393b;
    --brand-red: #c01f25;
    --ink-light: #ffffff;
    --divider: #6a6a6c;
  }
  * { margin: 0; padding: 0; box-sizing: border-box; }
  html, body {
    width: 1200px; height: 987px; overflow: hidden;
    background: var(--backdrop);
    font-family: "Source Sans 3", "Myriad Pro", Arial, sans-serif;
  }
  .stage { position: relative; width: 1200px; height: 987px; }

  .card {
    position: absolute; left: 293px; width: 615px; height: 352px; overflow: hidden;
  }
  .card--front { top: 130px; background: var(--paper); }
  .card--back  { top: 505px; background: var(--brand-red); }

  .card__bands { position: absolute; inset: 0; width: 100%; height: 100%; }

  .brand {
    position: absolute; top: 62px; left: 0; width: 100%; height: 82px;
    display: flex; justify-content: center; align-items: center; gap: 16px;
  }
  .brand__square { width: 82px; height: 82px; background: var(--brand-red); flex: none; }
  .brand__name {
    font-size: 44px; font-weight: 600; color: var(--charcoal); line-height: 1;
  }

  .holder {
    position: absolute; right: 356px; top: 264px; text-align: right;
  }
  .holder__name {
    font-size: 22px; font-weight: 400; color: var(--brand-red);
    text-transform: uppercase; line-height: 26px;
  }
  .holder__title { font-size: 17px; color: var(--ink-light); line-height: 22px; }

  .card__divider {
    position: absolute; left: 281px; top: 251px; width: 1px; height: 70px; background: var(--divider);
  }

  .contact { position: absolute; left: 303px; top: 252px; list-style: none; }
  .contact__item {
    display: flex; align-items: center; gap: 9px;
    height: 23.5px; font-size: 17px; color: var(--ink-light);
  }
  .contact__icon { width: 13px; height: 13px; fill: var(--brand-red); flex: none; }

  .back-brand {
    position: absolute; right: 52px; top: 185px; height: 120px;
    display: flex; align-items: center; gap: 16px;
  }
  .back-brand__square { width: 120px; height: 120px; background: var(--ink-light); flex: none; }
  .back-brand__name { font-size: 30px; font-weight: 600; color: var(--ink-light); line-height: 1; }

  .back-url {
    position: absolute; right: 38px; top: 313px;
    font-size: 17px; font-style: italic; color: var(--ink-light); line-height: 1.2;
  }
</style>
</head>
<body>
<main class="stage">

  <section class="card card--front" aria-label="Card front">
    <svg class="card__bands" viewBox="0 0 525 300" preserveAspectRatio="none" aria-hidden="true">
      <polygon points="0,172 320,172 313,179 0,179" fill="var(--brand-red)"/>
      <polygon points="0,180 315,180 325,161 525,161 525,300 0,300" fill="var(--charcoal)"/>
    </svg>

    <div class="brand">
      <span class="brand__square"></span>
      <span class="brand__name">Kestrany</span>
    </div>

    <div class="holder">
      <p class="holder__name">Dana Whitfield</p>
      <p class="holder__title">CEO/Founder</p>
    </div>

    <span class="card__divider"></span>

    <ul class="contact">
      <li class="contact__item">
        <svg class="contact__icon" viewBox="0 0 10 10"><path d="M2 0.5 L3.6 2.6 L2.7 3.6 Q4 6 6.4 7.3 L7.4 6.4 L9.5 8 L8.3 9.5 Q3.5 9 0.5 1.7 Z"/></svg>
        <span>555 204 7731</span>
      </li>
      <li class="contact__item">
        <svg class="contact__icon" viewBox="0 0 10 10"><path d="M0 2 H10 V8.5 H0 Z M0 2 L5 5.5 L10 2" stroke="var(--charcoal)" stroke-width="0.8"/></svg>
        <span>dana@kestrany-insp.com</span>
      </li>
      <li class="contact__item">
        <svg class="contact__icon" viewBox="0 0 10 10"><circle cx="5" cy="5" r="5"/></svg>
        <span>www.kestrany-insp.com</span>
      </li>
    </ul>
  </section>

  <section class="card card--back" aria-label="Card back">
    <div class="back-brand">
      <span class="back-brand__name">Kestrany</span>
      <span class="back-brand__square"></span>
    </div>
    <p class="back-url">www.kestrany-insp.com</p>
  </section>

</main>
</body>
</html>
```